Modern Business Card For A Digital Advertising Company

I'll be print on the Pell Prints Velour paper http://us.pellprints.com/products/velour/business-cards.html
Need's to be modern and use the color palette of the logo or gray scales. I think integrating the pixelation of the logo in to the card and having it wrap from one side to the other could be interesting. My company provides ad operations, web development, and number of other services to websites around the world. You can see my website at http://www.zantorhq.com
Contact info on the card needs to have
Owen Lasko
President
p.318.204.6637
owen@zantorhq.com
http://www.zantorhq.com
Doesn't necessarily need to be in that order
Website owners
Business

```html
<!DOCTYPE html>
<html lang="en">
<head>
<meta charset="utf-8">
<title>Zantor HQ — Business Card</title>
<link href="https://fonts.googleapis.com/css2?family=Arimo:wght@400;700&display=swap" rel="stylesheet">
<style>
  :root {
    --stage: #808080;
    --black: #000000;
    --white: #ffffff;
    --green: #8cc63f;
    --lime: #b2e05a;
    --band-gray: #3c3c3c;
    --text-light: #f2f2f2;
  }
  * { margin: 0; padding: 0; box-sizing: border-box; }
  html, body { width: 1200px; height: 392px; overflow: hidden; }
  body {
    background: var(--stage);
    font-family: "Arimo", Arial, sans-serif;
    position: relative;
  }
  .card { position: absolute; width: 560px; height: 322px; overflow: hidden; }

  /* Front side */
  .card--front { left: 34px; top: 34px; background: var(--black); }
  .front-frame {
    position: absolute; left: 34px; top: 41px; width: 494px; height: 234px;
    background: var(--lime); border-radius: 40px;
  }
  .front-panel {
    position: absolute; left: 14px; top: 12px; right: 14px; bottom: 12px;
    background: var(--white); border-radius: 30px;
    display: flex; align-items: center; justify-content: center;
  }

  /* Wordmark */
  .wordmark {
    display: flex; align-items: center; gap: 12px;
    color: var(--green); font-weight: 700; letter-spacing: 2px;
  }
  .wordmark__square { background: var(--green); }
  .wordmark--large { font-size: 40px; }
  .wordmark--large .wordmark__square { width: 30px; height: 30px; }
  .wordmark--small { font-size: 28px; gap: 9px; }
  .wordmark--small .wordmark__square { width: 21px; height: 21px; }

  /* Back side */
  .card--back { left: 612px; top: 32px; background: var(--white); width: 560px; height: 323px; }
  .back-logo {
    position: absolute; left: 0; right: 0; top: 62px; height: 110px;
    display: flex; align-items: center; justify-content: center;
  }
  .contact-band { position: absolute; left: 0; right: 0; top: 204px; bottom: 0; background: var(--black); }
  .contact-band__rule {
    position: absolute; left: 0; right: 0; height: 2px;
    background: linear-gradient(90deg, #222 0%, #cfcfcf 50%, #222 100%);
  }
  .contact-band__rule--top { top: 16px; }
  .contact-band__rule--bottom { top: 74px; }
  .contact-band__panel {
    position: absolute; left: 0; right: 0; top: 18px; height: 56px;
    background: linear-gradient(180deg, #474747 0%, var(--band-gray) 100%);
  }
  .person { position: absolute; left: 34px; top: 6px; }
  .person__name { color: var(--lime); font-weight: 700; font-size: 20px; line-height: 24px; }
  .person__title { color: var(--text-light); font-size: 15px; line-height: 20px; }
  .contacts { position: absolute; left: 337px; top: 5px; }
  .contacts__row {
    display: flex; align-items: center; gap: 9px;
    color: var(--lime); font-size: 15px; line-height: 24px;
  }
  .contacts__icon { width: 14px; height: 14px; flex: none; }
  .website {
    position: absolute; left: 0; right: 0; top: 85px;
    text-align: center; color: var(--lime); font-size: 16px; letter-spacing: 0.3px;
  }
</style>
</head>
<body>
  <section class="card card--front" aria-label="Card front">
    <div class="front-frame">
      <div class="front-panel">
        <div class="wordmark wordmark--large">
          <span class="wordmark__square"></span>
          <span class="wordmark__name">ZANTOR HQ</span>
        </div>
      </div>
    </div>
  </section>

  <section class="card card--back" aria-label="Card back">
    <div class="back-logo">
      <div class="wordmark wordmark--small">
        <span class="wordmark__square"></span>
        <span class="wordmark__name">ZANTOR HQ</span>
      </div>
    </div>

    <div class="contact-band">
      <div class="contact-band__panel">
        <div class="person">
          <p class="person__name">Owen Lasko</p>
          <p class="person__title">President</p>
        </div>
        <div class="contacts">
          <p class="contacts__row">
            <svg class="contacts__icon" viewBox="0 0 14 14" aria-hidden="true">
              <circle cx="7" cy="7" r="6.2" fill="none" stroke="currentColor" stroke-width="1.1"/>
              <path d="M4.8 3.8 L6 3.6 L6.6 5.4 L5.8 6 Q6.4 7.6 8 8.3 L8.6 7.5 L10.3 8.1 L10.1 9.3 Q7.6 10 5.6 7.9 Q4.2 6.2 4.8 3.8 Z" fill="currentColor"/>
            </svg>
            <span>318-204-6637</span>
          </p>
          <p class="contacts__row">
            <svg class="contacts__icon" viewBox="0 0 14 14" aria-hidden="true">
              <rect x="1" y="3" width="12" height="8.5" fill="none" stroke="currentColor" stroke-width="1.1"/>
              <path d="M1 3 L7 8 L13 3" fill="none" stroke="currentColor" stroke-width="1.1"/>
            </svg>
            <span>owen@zantorhq.com</span>
          </p>
        </div>
      </div>
      <div class="contact-band__rule contact-band__rule--top"></div>
      <div class="contact-band__rule contact-band__rule--bottom"></div>
      <p class="website">www.zantorhq.com</p>
    </div>
  </section>
</body>
</html>
```